We need a flyer designed for our 4th Annual Harvestlight: A Kinfolk Homecoming for the Heritage Festival that includes the day, time, location, address, and logos. It also needs to include what to expect. The event will be held on Saturday June 14th from 12p-6p at Cedar Commons located at 417 N. Bellmora St., Pensacola, FL 32507. Please see uploaded files for prior flyers for reference when it comes to information to include. Also I've uploaded pictures from our prior festivals that you may incorporate and logos.

```html
<!DOCTYPE html>
<html lang="en">
<head>
<meta charset="utf-8">
<title>Harvestlight – A Kinfolk Homecoming for the Heritage Festival</title>
<link rel="stylesheet" href="https://fonts.googleapis.com/css2?family=Anton&family=Open+Sans:wght@700;800&display=swap">
<style>
  :root {
    --ink: #111111;
    --white: #ffffff;
    --yellow: #ffea00;
    --gold: #f2a93b;
    --cream: #fdf0c4;
    --rule: #555555;
    --l-orange: #f7b548;
    --l-blue: #2bc0ea;
    --l-green: #8cc63f;
    --l-pink: #e597c4;
    --l-tan: #ebb57c;
    --l-teal: #7ecfce;
    --l-violet: #b98dc2;
    --l-sky: #b9e2f7;
    --l-lemon: #e8e77a;
    --l-salmon: #eeaa9a;
    --l-coral: #f38f6e;
  }
  * { margin: 0; padding: 0; box-sizing: border-box; }
  html, body { width: 927px; height: 1200px; overflow: hidden; background: var(--white); }
  .flyer {
    position: relative;
    width: 927px;
    height: 1200px;
    overflow: hidden;
    font-family: "Open Sans", Arial, sans-serif;
  }
  .backdrop {
    position: absolute;
    inset: 0;
    background:
      conic-gradient(from 200deg at 62% 62%,
        #f5d90a 0deg, #f7a21b 40deg, #ef3b2d 80deg, #e2127a 120deg,
        #7a3fa0 160deg, #1e8fd6 200deg, #17a34a 240deg, #c9d82b 280deg,
        #ffe81a 320deg, #f5d90a 360deg);
  }
  .footer-band { position: absolute; left: 0; top: 1000px; width: 927px; height: 200px; }

  .presenter {
    position: absolute;
    left: 400px;
    top: 92px;
    display: flex;
    align-items: center;
    gap: 14px;
  }
  .presenter-dot { width: 32px; height: 32px; border-radius: 50%; background: var(--ink); flex: none; }
  .presenter-name {
    font-weight: 800;
    font-size: 30px;
    line-height: 34px;
    color: var(--ink);
    text-transform: uppercase;
  }
  .presents {
    position: absolute;
    left: 559px;
    top: 168px;
    width: 180px;
    text-align: center;
    font-weight: 800;
    font-size: 24px;
    line-height: 30px;
    color: var(--ink);
  }
  .edition {
    position: absolute;
    left: 517px;
    top: 202px;
    width: 240px;
    text-align: center;
    font-weight: 800;
    font-size: 35px;
    line-height: 44px;
    color: var(--ink);
  }
  .edition sup { font-size: 20px; }

  .title { position: absolute; left: 0; top: 0; width: 927px; height: 820px; }
  .title text { font-family: "Anton", Impact, sans-serif; }
  .title .shadow { fill: var(--ink); }
  .title .face { stroke: var(--white); stroke-width: 5; paint-order: stroke; }

  .tagline {
    position: absolute;
    left: 83px;
    top: 811px;
    width: 751px;
    height: 53px;
    border-radius: 27px;
    background: var(--ink);
    color: var(--yellow);
    font-weight: 700;
    font-size: 28px;
    display: flex;
    align-items: center;
    justify-content: center;
    white-space: nowrap;
  }

  .when { position: absolute; left: 187px; top: 860px; width: 340px; height: 190px; }
  .when .display { font-family: "Anton", Impact, sans-serif; }
  .when .time { font-family: "Open Sans", Arial, sans-serif; font-weight: 800; }
  .when .shade { fill: var(--ink); }

  .venue { position: absolute; left: 549px; top: 885px; width: 216px; }
  .venue-pill {
    height: 61px;
    margin-bottom: 7px;
    border-radius: 30px;
    background: var(--cream);
    color: var(--ink);
    font-weight: 700;
    font-size: 17px;
    line-height: 21px;
    text-align: center;
    display: flex;
    align-items: center;
    justify-content: center;
  }

  .highlights {
    position: absolute;
    left: 34px;
    top: 1072px;
    width: 560px;
    text-align: center;
    color: var(--gold);
    font-weight: 700;
    font-size: 18.5px;
    line-height: 25px;
    text-transform: uppercase;
  }
  .footer-rule { position: absolute; left: 593px; top: 1064px; width: 1px; height: 106px; background: var(--rule); }
  .sponsor {
    position: absolute;
    left: 632px;
    top: 1101px;
    width: 237px;
    height: 53px;
    background: #1c1c1c;
    display: flex;
    align-items: center;
    justify-content: center;
    gap: 10px;
  }
  .sponsor-mark { width: 26px; height: 26px; background: var(--gold); }
  .sponsor-name { color: var(--white); font-weight: 700; font-size: 15px; }
</style>
</head>
<body>
<main class="flyer">
  <div class="backdrop" role="img" aria-label="Vibrant radiating bands of yellow, orange, red, magenta, purple, blue and green with paint splatters"></div>

  <svg class="footer-band" viewBox="0 0 927 200" aria-hidden="true">
    <path d="M0 26 C 300 58, 620 58, 927 6 L927 200 L0 200 Z" fill="#000"/>
  </svg>

  <div class="presenter">
    <span class="presenter-dot"></span>
    <span class="presenter-name">The Marlow Kin<br>Foundation</span>
  </div>
  <div class="presents">PRESENT</div>
  <div class="edition">4<sup>th</sup> Annual</div>

  <svg class="title" viewBox="0 0 927 820" aria-label="Harvestlight">
    <text class="shadow" x="109" y="572" font-size="357" textLength="714" lengthAdjust="spacingAndGlyphs">HARVEST</text>
    <text class="face" x="102" y="565" font-size="357" textLength="714" lengthAdjust="spacingAndGlyphs"><tspan fill="var(--l-orange)">H</tspan><tspan fill="var(--l-blue)">A</tspan><tspan fill="var(--l-green)">R</tspan><tspan fill="var(--l-pink)">V</tspan><tspan fill="var(--l-coral)">E</tspan><tspan fill="var(--l-lemon)">S</tspan><tspan fill="var(--l-sky)">T</tspan></text>
    <text class="shadow" x="77" y="802" font-size="247" textLength="769" lengthAdjust="spacingAndGlyphs">LIGHT</text>
    <text class="face" x="70" y="795" font-size="247" textLength="769" lengthAdjust="spacingAndGlyphs"><tspan fill="var(--l-tan)">L</tspan><tspan fill="var(--l-teal)">I</tspan><tspan fill="var(--l-violet)">G</tspan><tspan fill="var(--l-sky)">H</tspan><tspan fill="var(--l-salmon)">T</tspan></text>
  </svg>

  <div class="tagline">A Kinfolk Homecoming for the Heritage Festival</div>

  <svg class="when" viewBox="0 0 340 190" aria-label="Saturday June 14th, 12PM to 6PM">
    <text class="display shade" x="172" y="60" font-size="40" text-anchor="middle" letter-spacing="1">SATURDAY</text>
    <text class="display" x="170" y="58" font-size="40" text-anchor="middle" letter-spacing="1" fill="var(--white)">SATURDAY</text>
    <text class="display shade" x="173" y="140" font-size="86" text-anchor="middle">June 14<tspan font-size="46" dy="-38">th</tspan></text>
    <text class="display" x="170" y="137" font-size="86" text-anchor="middle" fill="var(--yellow)">June 14<tspan font-size="46" dy="-38">th</tspan></text>
    <text class="time" x="170" y="171" font-size="29" text-anchor="middle" fill="var(--white)">12PM-6PM</text>
  </svg>

  <div class="venue">
    <div class="venue-pill">at CEDAR COMMONS<br>located at 417 N.</div>
    <div class="venue-pill">Bellmora St.,<br>Pensacola, FL 32507.</div>
  </div>

  <div class="highlights">
    Live Performances | Food Vendors |<br>
    Art/African Clothing | Kids Obstacle Course &amp;<br>
    Play Area | Spades &amp; Domino Tables |<br>
    Bring Your Own Chairs or Picnic Blankets
  </div>
  <div class="footer-rule"></div>
  <div class="sponsor">
    <span class="sponsor-mark"></span>
    <span class="sponsor-name">The Marlow Firm, PLLC</span>
  </div>
</main>
</body>
</html>
```